Need CATCHY/VIVID Banner design for my new UTV/ATV/Off Road Vehicle turn signal/lighting company

I need a banner ad designed so I can advertise on several different ATV (all terrain vehicle), UTV (Utility Vehicles), Golf Cart and Off-Road Vehicle forums. Ads need to be very catchy and produce a call to action. Action is getting hits to my website. Our main business is selling turn signal kits to make your side by side or your ATV/UTV street legal, as some states now allow you to drive these on public roads if you have the following items: Turn Signals, Horn, Lighted license plate bracket, headlights and brake lights. We sell all of these items for just about any model vehicle out there. Our call to action for this banner would be to get more website visits.

Target Market(s)

Off-road/outdoor enthusiasts,

Industry/Entity Type

Car Accessorie

Font styles to use
Sans Serif

Requirements
Must have
• Ad size need to be either 728x90 or 300x250. Colorful ad with an off-road vehicle integrated to the design (think UTV, side-by-side, etc.
Nice to have
• Nice to haves would be anything that makes this banner ad stand out on very boring web pages.
Should not have
• anything dull

```html
<!DOCTYPE html>
<html lang="en">
<head>
<meta charset="utf-8">
<title>TrailBlink – ATV &amp; UTV Signal Lighting Banner</title>
<link rel="stylesheet" href="https://fonts.googleapis.com/css2?family=Montserrat:wght@600;700;800&display=swap">
<style>
  :root {
    --navy: #1a1f2b;
    --navy-deep: #12161f;
    --red: #e8262b;
    --red-dark: #b4151a;
    --yellow: #ffc21a;
    --white: #ffffff;
    --ink: #1b1b1b;
    --sand-light: #c9a27a;
    --sand-mid: #8f6a4a;
    --sand-dark: #4a3526;
  }
  html, body {
    margin: 0;
    padding: 0;
    overflow: hidden;
    background: #ffffff;
  }
  .banner {
    position: relative;
    width: 1200px;
    height: 1000px;
    overflow: hidden;
    font-family: "Montserrat", Arial, sans-serif;
    color: var(--white);
  }
  .vehicle-scene {
    position: absolute;
    inset: 0;
    background:
      radial-gradient(ellipse at 75% 45%, #2a2a2e 0%, #2a2a2e 18%, transparent 42%),
      linear-gradient(180deg, #a98a6e 0%, var(--sand-light) 22%, var(--sand-mid) 55%, var(--sand-dark) 100%);
  }
  .shapes {
    position: absolute;
    inset: 0;
  }
  .brand {
    position: absolute;
    left: 44px;
    top: 96px;
    width: 520px;
    text-align: center;
  }
  .brand-name {
    font-weight: 800;
    font-size: 64px;
    letter-spacing: 1px;
    color: var(--red);
    line-height: 1;
    margin: 0 0 36px;
  }
  .brand-tagline {
    font-weight: 800;
    font-size: 34px;
    line-height: 1.08;
    letter-spacing: 0.5px;
    margin: 0;
    text-transform: uppercase;
  }
  .brand-tagline span {
    display: block;
    font-size: 27px;
  }
  .headline {
    position: absolute;
    left: 50px;
    top: 480px;
    margin: 0;
    font-weight: 700;
    font-size: 92px;
    line-height: 1.08;
    letter-spacing: 1px;
    text-transform: uppercase;
  }
  .subhead {
    position: absolute;
    left: 52px;
    top: 690px;
    margin: 0;
    font-weight: 700;
    font-size: 51px;
    letter-spacing: 1px;
    color: var(--red);
    text-transform: uppercase;
  }
  .cta {
    position: absolute;
    left: 118px;
    top: 792px;
    width: 378px;
    height: 102px;
    border-radius: 51px;
    background: var(--red);
    color: var(--white);
    font-weight: 800;
    font-size: 29px;
    letter-spacing: 0.5px;
    text-decoration: none;
    display: flex;
    align-items: center;
    justify-content: center;
    gap: 18px;
  }
  .features {
    position: absolute;
    right: 20px;
    bottom: 14px;
    display: flex;
    gap: 44px;
    align-items: center;
  }
</style>
</head>
<body>
  <div class="banner">
    <div class="vehicle-scene" role="img" aria-label="Photo of a black side-by-side UTV with red roll cage climbing rocks in a desert canyon"></div>

    <svg class="shapes" width="1200" height="1000" viewBox="0 0 1200 1000" aria-hidden="true">
      <defs>
        <linearGradient id="edge-glow" x1="0" y1="0" x2="0" y2="1">
          <stop offset="0" stop-color="#e8262b"/>
          <stop offset="0.6" stop-color="#e8262b" stop-opacity="0.6"/>
          <stop offset="1" stop-color="#e8262b" stop-opacity="0"/>
        </linearGradient>
      </defs>
      <polygon class="panel" points="0,0 494,0 752,1000 0,1000" fill="var(--navy)"/>
      <polygon class="panel-edge" points="494,0 512,0 770,1000 752,1000" fill="url(#edge-glow)"/>
      <polygon class="corner-accent" points="0,0 200,0 0,96" fill="var(--red-dark)"/>
      <polygon class="corner-accent-light" points="0,0 130,0 0,60" fill="var(--red)"/>
      <polygon class="feature-band" points="668,1000 1200,826 1200,1000" fill="var(--yellow)"/>
    </svg>

    <div class="brand">
      <p class="brand-name">TRAILBLINK</p>
      <p class="brand-tagline">Turn Signal Kits<span>&amp; Lighting Accessories</span></p>
    </div>

    <h1 class="headline">ATV&amp; UTV<br>Vechicle</h1>
    <p class="subhead">Signal Lighting</p>

    <a class="cta" href="#">LEARN MORE
      <svg width="20" height="26" viewBox="0 0 20 26" aria-hidden="true"><path d="M4 3 L15 13 L4 23" fill="none" stroke="#fff" stroke-width="5" stroke-linecap="round" stroke-linejoin="round"/></svg>
    </a>

    <div class="features">
      <svg class="icon-brake" width="70" height="60" viewBox="0 0 70 60" aria-label="Brake lights">
        <circle cx="35" cy="30" r="18" fill="none" stroke="var(--ink)" stroke-width="5"/>
        <path d="M12 10 A28 28 0 0 0 12 50 M58 10 A28 28 0 0 1 58 50" fill="none" stroke="var(--ink)" stroke-width="5" stroke-linecap="round"/>
        <rect x="32" y="18" width="6" height="15" rx="2" fill="var(--ink)"/>
        <circle cx="35" cy="40" r="3.5" fill="var(--ink)"/>
      </svg>
      <svg class="icon-headlight" width="76" height="50" viewBox="0 0 76 50" aria-label="Headlights">
        <path d="M38 4 C18 4 10 14 10 25 C10 36 18 46 38 46 Z" fill="var(--ink)"/>
        <path d="M46 10 H72 M46 20 H72 M46 30 H72 M46 40 H72" stroke="var(--ink)" stroke-width="6" stroke-linecap="round"/>
      </svg>
      <svg class="icon-horn" width="96" height="66" viewBox="0 0 96 66" aria-label="Horn">
        <path d="M20 30 H34 L66 14 V52 L34 36 H20 Z" fill="none" stroke="var(--ink)" stroke-width="5" stroke-linejoin="round"/>
        <rect x="24" y="36" width="8" height="14" fill="var(--ink)"/>
        <path d="M76 33 H90 M74 20 L86 12 M74 46 L86 54 M4 33 H14 M8 18 L16 24 M8 48 L16 42" stroke="var(--ink)" stroke-width="4" stroke-linecap="round"/>
        <path d="M46 4 V10 M58 2 V8" stroke="var(--ink)" stroke-width="4" stroke-linecap="round"/>
      </svg>
      <svg class="icon-turn" width="100" height="60" viewBox="0 0 100 60" aria-label="Turn signals">
        <path d="M26 6 L4 30 L26 54 V40 H42 V20 H26 Z" fill="none" stroke="var(--ink)" stroke-width="5" stroke-linejoin="round"/>
        <path d="M74 6 L96 30 L74 54 V40 H58 V20 H74 Z" fill="none" stroke="var(--ink)" stroke-width="5" stroke-linejoin="round"/>
      </svg>
    </div>
  </div>
</body>
</html>
```